Hair Salon using organic products looking for AWSOME new menu's!!

We want different and fun incorporating our logo. We would love a folding or tri-folding menu. Any ideas would be welcome we like different. We are an tolmi salon in a little colonial town, but don't like the colonial feel. we would like menu's that would not cost an arm and a leg to print. And we could update as prices and services change without having to re-do the entire design.

Target Market(s)

upper class clients with an interest in using plant based products on their hair and skin

Industry/Entity Type

Hair And Beauty

Requirements
Must have
• Logo, area for contact information and ability to list all salon services
Nice to have
• just a really fun different look to set us aside from other salons. We like to be different

```html
<!DOCTYPE html>
<html lang="en">
<head>
<meta charset="utf-8">
<title>Lumen Salon – Service Menu</title>
<link rel="stylesheet" href="https://fonts.googleapis.com/css2?family=Cinzel:wght@400;500&family=Cormorant+Garamond:wght@500;600&family=Tinos&family=Roboto:wght@400&display=swap">
<style>
  :root {
    --paper: #ffffff;
    --ink: #0b0a09;
    --panel: #0f0d0b;
    --panel-cover: #070707;
    --gold: #d4ad4a;
    --gold-soft: #b89338;
    --text: #e9e4da;
    --dots: #a88a3c;
  }
  * { margin: 0; padding: 0; box-sizing: border-box; }
  html, body {
    width: 898px; height: 1200px; overflow: hidden;
    background: var(--paper);
  }
  .menu-sheet {
    position: absolute; left: 20px; top: 338px;
    width: 858px; height: 523px;
    display: flex;
    background: var(--ink);
    box-shadow: 0 4px 14px rgba(0,0,0,0.35);
  }
  .panel { position: relative; height: 100%; }
  .panel--left { width: 284px; background: var(--panel); }
  .panel--middle { width: 288px; background: var(--panel); border-left: 1px solid rgba(212,173,74,0.35); }
  .panel--cover { width: 286px; background: linear-gradient(180deg, #111 0%, var(--panel-cover) 40%, #0d0d0d 100%); }

  .products-backdrop {
    position: absolute; left: 0; bottom: 0; width: 572px; height: 170px;
    background:
      radial-gradient(ellipse 70px 55px at 55px 120px, rgba(214,196,170,0.55), transparent 70%),
      radial-gradient(ellipse 80px 65px at 285px 120px, rgba(196,130,100,0.55), transparent 70%),
      radial-gradient(ellipse 110px 70px at 480px 110px, rgba(150,120,100,0.45), transparent 70%),
      linear-gradient(180deg, rgba(15,13,11,0) 0%, rgba(60,48,40,0.45) 100%);
  }
  .menu-column { position: absolute; top: 0; left: 0; width: 100%; height: 100%; z-index: 1; }

  .section-heading {
    position: absolute; height: 25px;
    border: 1px solid var(--gold);
    display: flex; align-items: center; justify-content: center; gap: 6px;
    font-family: "Cormorant Garamond", serif; font-weight: 600;
    font-size: 19px; color: var(--gold);
  }
  .section-heading .fleuron { width: 14px; height: 10px; }

  .price-list { position: absolute; list-style: none; }
  .price-row {
    display: flex; align-items: baseline; height: 20.5px;
    font-family: "Tinos", serif; font-size: 11px; color: var(--text);
  }
  .price-row .leader { flex: 1; border-bottom: 1px dotted var(--dots); margin: 0 6px; transform: translateY(-3px); }
  .price-row .price { width: 22px; text-align: right; }

  .menu-title {
    position: absolute; left: 80px; top: 24px; width: 130px;
    border-top: 1px solid var(--gold-soft); border-bottom: 1px solid var(--gold-soft);
    text-align: center;
    font-family: "Cinzel", serif; font-size: 34px; line-height: 40px;
    color: var(--gold);
  }

  .brand {
    position: absolute; top: 22px; left: 0; width: 100%;
    display: flex; flex-direction: column; align-items: center; gap: 18px;
  }
  .brand-mark { width: 54px; height: 54px; border-radius: 50%; border: 1.5px solid var(--gold); }
  .brand-name {
    font-family: "Cinzel", serif; font-size: 18px; letter-spacing: 4px;
    color: var(--gold);
  }
  .salon-photo {
    position: absolute; left: 0; top: 168px; width: 100%; height: 250px;
    border-top: 2px solid var(--gold); border-bottom: 2px solid var(--gold);
    background:
      radial-gradient(ellipse 60px 80px at 130px 90px, rgba(110,160,200,0.55), transparent 70%),
      radial-gradient(ellipse 60px 50px at 90px 190px, rgba(210,190,165,0.55), transparent 70%),
      linear-gradient(180deg, #2b3340 0%, #1b1d22 50%, #3a2f26 100%);
  }
  .site-url {
    position: absolute; bottom: 16px; width: 100%; text-align: center;
    font-family: "Roboto", sans-serif; font-size: 9px; letter-spacing: 2px;
    color: var(--gold);
  }
</style>
</head>
<body>
<svg width="0" height="0" style="position:absolute">
  <symbol id="fleuron" viewBox="0 0 14 10">
    <path d="M7 1 C5 3 5 5 7 9 C9 5 9 3 7 1 Z M1 6 C3 3 6 4 7 7 M13 6 C11 3 8 4 7 7" fill="none" stroke="#d4ad4a" stroke-width="1"/>
  </symbol>
</svg>

<main class="menu-sheet">
  <section class="panel panel--left">
    <div class="products-backdrop" role="img" aria-label="Makeup products: powder compact, brush and bronzing pearls"></div>
    <div class="menu-column">
      <h2 class="section-heading" style="left:30px;top:27px;width:220px"><svg class="fleuron"><use href="#fleuron"/></svg>Heading<svg class="fleuron"><use href="#fleuron"/></svg></h2>
      <ul class="price-list" style="left:30px;top:56px;width:222px">
        <li class="price-row"><span>Lorem Ipsum</span><span class="leader"></span><span class="price">$ 10</span></li>
        <li class="price-row"><span>Lorem Ipsum</span><span class="leader"></span><span class="price">$ 10</span></li>
        <li class="price-row"><span>Lorem Ipsum</span><span class="leader"></span><span class="price">$ 10</span></li>
        <li class="price-row"><span>Lorem Ipsum</span><span class="leader"></span><span class="price">$ 10</span></li>
      </ul>
      <h2 class="section-heading" style="left:30px;top:146px;width:220px"><svg class="fleuron"><use href="#fleuron"/></svg>Heading<svg class="fleuron"><use href="#fleuron"/></svg></h2>
      <ul class="price-list" style="left:30px;top:177px;width:222px">
        <li class="price-row"><span>Lorem Ipsum</span><span class="leader"></span><span class="price">$ 10</span></li>
        <li class="price-row"><span>Lorem Ipsum</span><span class="leader"></span><span class="price">$ 10</span></li>
        <li class="price-row"><span>Lorem Ipsum</span><span class="leader"></span><span class="price">$ 10</span></li>
        <li class="price-row"><span>Lorem Ipsum</span><span class="leader"></span><span class="price">$ 10</span></li>
      </ul>
      <h2 class="section-heading" style="left:30px;top:265px;width:220px"><svg class="fleuron"><use href="#fleuron"/></svg>Heading<svg class="fleuron"><use href="#fleuron"/></svg></h2>
      <ul class="price-list" style="left:30px;top:298px;width:222px">
        <li class="price-row"><span>Lorem Ipsum</span><span class="leader"></span><span class="price">$ 10</span></li>
        <li class="price-row"><span>Lorem Ipsum</span><span class="leader"></span><span class="price">$ 10</span></li>
        <li class="price-row"><span>Lorem Ipsum</span><span class="leader"></span><span class="price">$ 10</span></li>
        <li class="price-row"><span>Lorem Ipsum</span><span class="leader"></span><span class="price">$ 10</span></li>
        <li class="price-row"><span>Lorem Ipsum</span><span class="leader"></span><span class="price">$ 10</span></li>
        <li class="price-row"><span>Lorem Ipsum</span><span class="leader"></span><span class="price">$ 10</span></li>
        <li class="price-row"><span>Lorem Ipsum</span><span class="leader"></span><span class="price">$ 10</span></li>
        <li class="price-row"><span>Lorem Ipsum</span><span class="leader"></span><span class="price">$ 10</span></li>
      </ul>
    </div>
  </section>

  <section class="panel panel--middle">
    <div class="menu-column">
      <h1 class="menu-title">MENU</h1>
      <h2 class="section-heading" style="left:35px;top:87px;width:220px"><svg class="fleuron"><use href="#fleuron"/></svg>Heading<svg class="fleuron"><use href="#fleuron"/></svg></h2>
      <ul class="price-list" style="left:35px;top:117px;width:222px">
        <li class="price-row"><span>Lorem Ipsum</span><span class="leader"></span><span class="price">$ 10</span></li>
        <li class="price-row"><span>Lorem Ipsum</span><span class="leader"></span><span class="price">$ 10</span></li>
        <li class="price-row"><span>Lorem Ipsum</span><span class="leader"></span><span class="price">$ 10</span></li>
        <li class="price-row"><span>Lorem Ipsum</span><span class="leader"></span><span class="price">$ 10</span></li>
      </ul>
      <h2 class="section-heading" style="left:35px;top:220px;width:220px"><svg class="fleuron"><use href="#fleuron"/></svg>Heading<svg class="fleuron"><use href="#fleuron"/></svg></h2>
      <ul class="price-list" style="left:35px;top:251px;width:222px">
        <li class="price-row"><span>Lorem Ipsum</span><span class="leader"></span><span class="price">$ 10</span></li>
        <li class="price-row"><span>Lorem Ipsum</span><span class="leader"></span><span class="price">$ 10</span></li>
        <li class="price-row"><span>Lorem Ipsum</span><span class="leader"></span><span class="price">$ 10</span></li>
        <li class="price-row"><span>Lorem Ipsum</span><span class="leader"></span><span class="price">$ 10</span></li>
        <li class="price-row"><span>Lorem Ipsum</span><span class="leader"></span><span class="price">$ 10</span></li>
        <li class="price-row"><span>Lorem Ipsum</span><span class="leader"></span><span class="price">$ 10</span></li>
      </ul>
    </div>
  </section>

  <section class="panel panel--cover">
    <header class="brand">
      <span class="brand-mark"></span>
      <span class="brand-name">LUMEN SALON</span>
    </header>
    <div class="salon-photo" role="img" aria-label="Salon interior with styling chairs, mirrors and product shelves"></div>
    <p class="site-url">www.lumensalon.com</p>
  </section>
</main>
</body>
</html>
```